Employment Agency Website Design

We are working with an employment agency in California.

Some sites to use for content/competitors and inspiration:

https://www.pinecrestjobs.com/us/en
https://www.velmorusa.com
https://www.dravenworks.us
https://www.quillora.com/en
https://www.tomvalusa.com
https://www.fernstaffing.com

Thank you for taking the time to consider designing a website for us. We are web developers based in Stockton, CA, USA. Most of our projects go through the same process. Understanding this process may help you win a project with us. We custom-code all of our websites in-house. We don’t have any requirements as to what tools you use for your design, but we prefer Framekit files. For any design that we label as four-stars, we send it to the client for review. The client picks the final design they want us to use. Once we complete this process, we will continue to show additional clients all the four-star sites and purchase them later. Your designs will have multiple chances to sell. For better chances of success, we ask that you follow these guidelines.

IMAGES:
If you use any images or icons in the design, we ask that you have a link to the asset so we can purchase the image/icon. Most of the designs we submit do not have the customer’s images on them unless they have some great images. Be creative; show us the feeling you are trying to portray with your image choices. Use any royalty-free site you choose. We subscribe to Adobe and mainly use their images, but we can purchase images outside of Adobe. PLEASE NOTE: we will not submit designs to clients with watermarks on the images.

FONTS:
We ask that you identify the fonts used in the design. This can be done in a message if you want. We typically use Google Fonts and Adobe Fonts.

CONTENT:
We're always open to different content and ideas. We often submit designs with stock images so the client can see our vision. We typically take pictures after the website launch to use their images with our vision. Lorem Ipsum is fine for paragraphs, but we ask that you write the headers in correct English. We want to be able to show the vision and identify the sections of the website.

INSPIRATION:
We typically add a couple of links in the brief of websites we like to help you get started in your design.

REVISIONS:
We do not often ask for revisions of the designs unless we see something in the design that may not appeal to the client. If there are slight changes that we want to make, we do that in the development process.

FEEDBACK:
We rarely give feedback on designs during the design process. We are working on many website projects and do not have the time to provide feedback. We usually respond if your request is well thought out and asks specific questions, but a note asking “feedback, please” usually goes unanswered.

```html
<!DOCTYPE html>
<html lang="en">
<head>
<meta charset="utf-8">
<title>Stride Talent — Your next growth opportunity</title>
<link href="https://fonts.googleapis.com/css2?family=Poppins:wght@500;600;700&family=Montserrat:wght@300;400;500;600;700&display=swap" rel="stylesheet">
<style>
:root{
  --red:#be1e2d;
  --red-soft:#c83844;
  --ink:#1f1f24;
  --muted:#8a8a96;
  --white:#ffffff;
  --lavender:#eef0fb;
  --blue:#4878a0;
  --green:#14a01e;
  --orange:#f4591f;
  --yellow:#f5b800;
}
*{box-sizing:border-box;margin:0;padding:0}
html,body{width:1200px;height:3989px;overflow:hidden}
body{position:relative;background:var(--white);font-family:"Montserrat",sans-serif;color:var(--ink)}
.abs{position:absolute}
h1,h2,h3,.brand{font-family:"Poppins",sans-serif}
.btn{position:absolute;display:flex;align-items:center;justify-content:center;font-size:13px;font-weight:600;border-radius:3px;text-decoration:none}
.btn-solid{background:var(--red);color:var(--white)}
.btn-outline{border:1.5px solid var(--red);color:var(--red);background:var(--white)}
.btn-white{background:var(--white);color:var(--red)}
.photo{position:absolute;border-radius:14px}

/* header */
.brand{display:flex;align-items:center;gap:8px;font-weight:600;font-size:16px;color:var(--red)}
.brand-mark{width:22px;height:22px;background:var(--red);border-radius:4px}
.nav a{position:absolute;top:46px;font-size:13px;color:var(--muted);text-decoration:none}
.nav a.active{color:var(--red);font-weight:700}

/* hero */
.hero-title{left:59px;top:280px;font-size:50px;line-height:60px;font-weight:700;letter-spacing:-1px}
.hero-text{left:59px;top:418px;width:620px;font-size:13px;line-height:24px;color:var(--muted)}
.profile{left:796px;top:492px;width:314px;height:298px;background:var(--white);border-radius:14px;box-shadow:0 20px 50px rgba(0,0,0,.12);padding:34px 40px}
.profile-name{font-family:"Poppins",sans-serif;font-size:24px;line-height:30px;font-weight:500}
.profile-role{font-size:9px;color:var(--muted);font-weight:400;margin-left:6px}
.exp{margin-top:16px;height:37px;background:var(--blue);color:var(--white);font-size:9px;display:flex;align-items:center;justify-content:center;border-radius:2px}
.skills{display:grid;grid-template-columns:repeat(3,1fr);gap:10px;margin-top:16px}
.skill{height:24px;font-size:9px;color:var(--white);display:flex;align-items:center;justify-content:center;border-radius:2px}
.g{background:var(--green)}.o{background:var(--orange)}.y{background:var(--yellow)}

/* options */
.section-title{left:0;width:1200px;text-align:center;font-weight:700;letter-spacing:-.5px}
.section-text{left:0;width:1200px;text-align:center;font-size:13px;line-height:25px;color:var(--muted)}
.option h3{position:absolute;font-size:20px;font-weight:700}
.option p{position:absolute;width:350px;font-size:13px;line-height:24px;color:var(--muted)}
.option a{position:absolute;font-size:14px;font-weight:700;color:var(--red);text-decoration:none}

/* red band */
.feature-title{font-size:25px;line-height:32px;font-weight:700;color:var(--white)}
.feature-text{font-size:12.5px;line-height:25px;color:var(--white)}
.ornament-area{position:absolute;background:var(--red-soft);opacity:.35;border-radius:8px}

/* testimonials */
.avatar{position:absolute;border-radius:50%;box-shadow:0 6px 16px rgba(0,0,0,.15)}
.quote-card{left:299px;top:2873px;width:602px;height:339px;background:var(--white);border-radius:16px;box-shadow:0 20px 40px rgba(120,120,180,.08)}
.quote{left:328px;top:2952px;width:544px;text-align:center;font-size:19.5px;line-height:36px;color:var(--muted);font-weight:300}
.pager{left:520px;top:3276px;display:flex;gap:17px}
.pager span{width:12px;height:12px;border-radius:50%;background:#c9c9d2}
.pager span.on{background:var(--red)}

/* footer */
.footer{left:0;top:3689px;width:1200px;height:300px;background:var(--red);color:var(--white)}
.footer a{position:absolute;top:200px;font-size:13px;color:var(--white);text-decoration:none;font-weight:500}
.social{position:absolute;left:0;width:1200px;top:240px;display:flex;justify-content:center;gap:28px}
.social a{position:static;font-size:12px;font-weight:500}
</style>
</head>
<body>

<header>
  <div class="abs brand" style="left:58px;top:22px;flex-direction:column;gap:4px;align-items:center">
    <span class="brand-mark"></span>
    <span>stridetalent</span>
  </div>
  <nav class="nav">
    <a class="active" href="#" style="left:198px">Home</a>
    <a href="#" style="left:272px">About Us</a>
    <a href="#" style="left:365px">For Companies</a>
    <a href="#" style="left:500px">For Talents</a>
    <a href="#" style="left:607px">Job Board</a>
    <a href="#" style="left:707px">Contact</a>
  </nav>
  <a class="btn btn-outline" href="#" style="left:870px;top:32px;width:115px;height:45px">Hire a Talent</a>
  <a class="btn btn-solid" href="#" style="left:998px;top:32px;width:143px;height:45px">Apply as a Talent</a>
</header>

<section>
  <h1 class="abs hero-title">Welcome to your next<br>growth opportunity</h1>
  <p class="abs hero-text">Get connected with full time, freelance and remote jobs that are suited just for you and meet your prerequisite.</p>
  <a class="btn btn-solid" href="#" style="left:59px;top:491px;width:141px;height:46px">Find a Job</a>
  <a class="btn btn-outline" href="#" style="left:221px;top:491px;width:155px;height:46px">Find a Talent</a>
  <div class="abs" style="left:1060px;top:560px;width:80px;height:90px;border-radius:40px;background:#f6dfe1"></div>
  <div class="photo" role="img" aria-label="Portrait of a smiling product designer with glasses" style="left:701px;top:150px;width:437px;height:502px;background:linear-gradient(160deg,#3a2d2a,#b88566 55%,#6b4a3c);box-shadow:0 10px 30px rgba(0,0,0,.15)"></div>
  <div class="abs profile">
    <div class="profile-name">Tobenna<br>Adeyemi<span class="profile-role">Product Designer</span></div>
    <div class="exp">5+ Years of Experience</div>
    <div class="skills">
      <span class="skill g">Framekit</span><span class="skill g">Protoly</span><span class="skill g">Drafto</span>
      <span class="skill o">HTML/CSS/JS</span><span class="skill o">Pressly</span><span></span>
      <span class="skill y">Pixelry</span><span class="skill y">Vectra</span><span class="skill y">Motiva</span>
    </div>
  </div>
</section>

<section>
  <h2 class="abs section-title" style="top:840px;font-size:42px">We open you up to a pool of possibilities.</h2>
  <p class="abs section-text" style="top:906px">Erase completely the stress and uncertainty of applying directly to companies, through job boards and dealing with a lot of recruiters.<br>StrideCo will link you with opportunities you want and at companies with similar interests.</p>

  <div class="option">
    <div class="photo" role="img" aria-label="Woman on a phone call by office blinds" style="left:57px;top:991px;width:348px;height:257px;background:linear-gradient(135deg,#e7e7e9,#b8aca2 60%,#4b3a33)"></div>
    <h3 style="left:57px;top:1266px">Full time</h3>
    <p style="left:57px;top:1301px">Join top companies anywhere in the world as a full time employee</p>
    <a href="#" style="left:57px;top:1371px">Learn More ›</a>
  </div>
  <div class="option">
    <div class="photo" role="img" aria-label="Two colleagues working at a laptop" style="left:426px;top:991px;width:346px;height:257px;background:linear-gradient(135deg,#d9d6d2,#8b6a55 55%,#eae8e6)"></div>
    <h3 style="left:426px;top:1266px">Part time</h3>
    <p style="left:426px;top:1301px">Work and Study? No Problem! We help you find the most suitable jobs for your schedule</p>
    <a href="#" style="left:426px;top:1371px">Learn More ›</a>
  </div>
  <div class="option">
    <div class="photo" role="img" aria-label="Freelancer working on a laptop in a bright loft" style="left:793px;top:991px;width:348px;height:257px;background:linear-gradient(135deg,#d7dde0,#8f8172 55%,#a0523f)"></div>
    <h3 style="left:793px;top:1266px">Freelance</h3>
    <p style="left:793px;top:1301px">Are one off gigs your preference? StrideCo helps you find freelance jobs of your choice</p>
    <a href="#" style="left:793px;top:1371px">Learn More ›</a>
  </div>
</section>

<section>
  <svg class="abs" style="left:0;top:1430px" width="1200" height="1230" viewBox="0 0 1200 1230">
    <path d="M0 13 Q600 40 1200 13 L1200 1210 Q600 1160 0 1210 Z" fill="var(--red)"/>
  </svg>
  <div class="ornament-area" role="img" aria-label="Decorative ring ornament" style="left:1025px;top:1445px;width:175px;height:210px"></div>
  <div class="ornament-area" role="img" aria-label="Decorative ring ornament" style="left:0;top:2455px;width:228px;height:180px"></div>

  <div class="photo" role="img" aria-label="Smiling woman on a phone call with a laptop" style="left:59px;top:1532px;width:346px;height:456px;background:linear-gradient(160deg,#4a4e5a,#c9a983 45%,#1e2433)"></div>
  <h2 class="abs feature-title" style="left:519px;top:1660px">A One-Stop Platform</h2>
  <p class="abs feature-text" style="left:519px;top:1705px;width:450px">You connect with Stride Talent We communicate with dozens of companies, platforms and hundreds of recruiters to single out the best opportunity for you!</p>
  <a class="btn btn-white" href="#" style="left:519px;top:1797px;width:148px;height:47px">Get Started</a>

  <div class="ornament-area" role="img" aria-label="Decorative dot pattern" style="left:60px;top:1993px;width:132px;height:132px"></div>

  <h2 class="abs feature-title" style="left:240px;top:2171px">Talent Centric Process,<br>Putting you FIRST!</h2>
  <p class="abs feature-text" style="left:240px;top:2248px;width:440px">StrideCo collaborates with companies who uphold the International standard hiring process. We ensure that good and structured career growth experiences are adopted for you.</p>
  <a class="btn btn-white" href="#" style="left:240px;top:2341px;width:150px;height:46px">Get Started</a>

  <div class="photo" role="img" aria-label="Professional woman working on a laptop on a sofa" style="left:794px;top:2011px;width:347px;height:455px;background:linear-gradient(160deg,#ece4d6,#2d3140 50%,#7a7a80)"></div>
  <div class="ornament-area" role="img" aria-label="Decorative dot pattern" style="left:854px;top:2478px;width:290px;height:36px"></div>
</section>

<section>
  <div class="abs" style="left:0;top:2640px;width:1200px;height:720px;background:linear-gradient(180deg,var(--white),var(--lavender) 50%,var(--white));z-index:-1"></div>
  <h2 class="abs section-title" style="top:2726px;font-size:40px;line-height:48px">Trusted by Talents<br>across the GLOBE!</h2>

  <div class="avatar" role="img" aria-label="Talent portrait" style="left:202px;top:2730px;width:98px;height:98px;background:#7c8f9a"></div>
  <div class="avatar" role="img" aria-label="Talent portrait" style="left:915px;top:2759px;width:68px;height:68px;background:#8a6e5c"></div>
  <div class="avatar" role="img" aria-label="Talent portrait" style="left:57px;top:2901px;width:68px;height:68px;background:#4e4a4c"></div>
  <div class="avatar" role="img" aria-label="Talent portrait" style="left:1027px;top:2945px;width:110px;height:110px;background:#3d5a2e"></div>
  <div class="avatar" role="img" aria-label="Talent portrait" style="left:103px;top:3131px;width:76px;height:76px;background:#6d6a6a"></div>
  <div class="avatar" role="img" aria-label="Talent portrait" style="left:956px;top:3219px;width:64px;height:64px;background:#2f9a86"></div>

  <div class="abs" style="left:340px;top:3160px;width:520px;height:70px;background:var(--white);border-radius:16px;box-shadow:0 10px 20px rgba(120,120,180,.08)"></div>
  <div class="abs quote-card"></div>
  <svg class="abs" style="left:500px;top:2940px" width="200" height="120" viewBox="0 0 200 120">
    <path d="M10 20 a30 30 0 1 1 40 40 l-25 50 h-15 l20-48 a30 30 0 0 1 -20 -42z M110 20 a30 30 0 1 1 40 40 l-25 50 h-15 l20-48 a30 30 0 0 1 -20 -42z" fill="#f7e3e5"/>
  </svg>
  <p class="abs quote">“The consultants that reached out to me about the role were super helpful, understanding and amazing. They were literally with me at every step from the interview to the waiting process and finally to getting the Job. Thank you Kayode and Folarin.”</p>

  <svg class="abs" style="left:428px;top:3270px" width="20" height="24" viewBox="0 0 20 24"><path d="M14 3 L5 12 L14 21" fill="none" stroke="var(--red)" stroke-width="3"/></svg>
  <div class="abs pager"><span class="on"></span><span></span><span></span><span></span><span></span><span></span></div>
  <svg class="abs" style="left:752px;top:3270px" width="20" height="24" viewBox="0 0 20 24"><path d="M6 3 L15 12 L6 21" fill="none" stroke="var(--red)" stroke-width="3"/></svg>
</section>

<section>
  <h2 class="abs section-title" style="top:3430px;font-size:41px">Get matched to your dream opportunity</h2>
  <p class="abs section-text" style="top:3494px">Save time and Focus your energy in getting one step closer to your next best opportunity.<br>Join our talent network now!</p>
  <a class="btn btn-solid" href="#" style="left:509px;top:3564px;width:181px;height:45px">Apply as a Talent</a>
</section>

<footer class="abs footer">
  <div class="abs brand" style="left:0;width:1200px;top:60px;flex-direction:column;gap:6px;color:var(--white)">
    <span class="brand-mark" style="background:var(--white)"></span>
    <span>stridetalent</span>
  </div>
  <p class="abs" style="left:0;width:1200px;top:131px;text-align:center;font-size:13px;letter-spacing:1px">We are a Recruiter Platform to help their get a employee</p>
  <a href="#" style="left:298px">About</a>
  <a href="#" style="left:407px">For Companies</a>
  <a href="#" style="left:574px">For Talents</a>
  <a href="#" style="left:713px">Job Board</a>
  <a href="#" style="left:848px">Contact</a>
  <div class="social">
    <a href="#">Lumo</a>
    <a href="#">Chirpr</a>
    <a href="#">Snapgrid</a>
  </div>
</footer>

</body>
</html>
```